Export company based in South America (Ecuador) we export flowers, chocolate, and bananas

We need a website that gives our potential clients and introduction into our company and the different types of commodities we export around the world. We are based in Quito, Ecuador so the website should portray the feel of Ecuadorian landscapes within a modern looking website.
At the moment we are exporting roses, chocolate, and bananas so the website should have an intro to our company and then three different areas that describe our three main commodity. The three different sections should explain why each of the products from Ecuador are some of the best in the world in their categories and the benefits of importing the commodity through our company.
Industry/Entity Type
Commodity
Number of Pages Required
4 page

```html
<!DOCTYPE html>
<html lang="en">
<head>
<meta charset="utf-8">
<title>Andina Trade Co. — Exporting Roses, Chocolate &amp; Bananas</title>
<link href="https://fonts.googleapis.com/css2?family=Josefin+Sans:wght@600;700&family=Poppins:wght@400;500;600&display=swap" rel="stylesheet">
<style>
:root{
  --navy:#1d3a5e;
  --navy-deep:#0f1b2b;
  --red:#e8343f;
  --pink-soft:#fde4e6;
  --ink:#1f2a37;
  --muted:#6b7480;
  --line:#d6dbe1;
  --green:#b7cf93;
  --yellow:#f8d98f;
  --salmon:#f5a68f;
  --white:#ffffff;
}
*{box-sizing:border-box;margin:0;padding:0}
html,body{width:1200px;height:3248px;overflow:hidden}
body{font-family:"Poppins",sans-serif;color:var(--ink);background:var(--white);position:relative}
h1,h2,h3{font-family:"Josefin Sans",sans-serif}
a{color:inherit;text-decoration:none}
.btn{display:inline-block;border-radius:24px;font-size:13px;font-weight:500;padding:12px 28px}
.btn-dark{background:var(--navy);color:var(--white)}

/* header */
.site-header{position:absolute;top:0;left:0;width:1200px;height:80px;display:flex;align-items:center;padding:0 160px;z-index:3}
.brand{display:flex;align-items:center;gap:10px}
.brand-mark{width:30px;height:30px;border-radius:50%;background:var(--red)}
.brand-name{font-family:"Poppins",sans-serif;font-weight:600;font-size:16px;color:var(--navy);line-height:1.05;width:90px}
.main-nav{display:flex;gap:8px;margin-left:180px}
.main-nav a{font-size:13px;padding:10px 16px;color:var(--ink)}
.main-nav a.active{background:var(--pink-soft);color:var(--red)}
.nav-phone{margin-left:140px;width:38px;height:38px;border-radius:50%;background:var(--red);display:flex;align-items:center;justify-content:center}
.nav-contact{margin-left:18px;padding:11px 26px}

/* hero */
.hero{position:absolute;top:0;left:0;width:1200px;height:600px}
.hero-copy{position:absolute;left:160px;top:170px;width:420px}
.hero-copy h1{font-size:38px;line-height:1.28;color:var(--navy);letter-spacing:1px}
.hero-copy h1 span{color:var(--red)}
.hero-copy p{font-size:13px;color:var(--muted);margin:22px 0 34px;line-height:1.7;width:330px}
.hero-bg{position:absolute;left:640px;top:80px;width:560px;height:500px;background:var(--navy);clip-path:polygon(8% 0,100% 0,100% 100%,20% 100%,0 55%)}
.photo{position:absolute;border-radius:4px}
.photo-cocoa{left:840px;top:80px;width:360px;height:240px;background:linear-gradient(135deg,#8a5a44,#c29a7f 50%,#6e4534)}
.photo-roses{left:600px;top:340px;width:220px;height:180px;background:linear-gradient(135deg,#b3223a,#e2546a 60%,#7a1428)}
.photo-bananas{left:840px;top:340px;width:360px;height:220px;background:linear-gradient(135deg,#e8c84a,#f3df7a 50%,#5c7b9c)}

/* benefits */
.benefits{position:absolute;top:680px;left:0;width:1200px;height:340px}
.feature{position:absolute;left:160px;width:420px;height:84px;border-radius:14px;display:flex;align-items:center;padding:0 22px;gap:18px;color:var(--white)}
.feature.green{top:0;background:var(--green)}
.feature.yellow{top:100px;background:var(--yellow)}
.feature.salmon{top:200px;background:var(--salmon);height:96px}
.feature-icon{width:46px;height:46px;border-radius:50%;border:2px solid var(--white);display:flex;align-items:center;justify-content:center;flex:none}
.feature h3{font-family:"Poppins",sans-serif;font-size:15px;font-weight:600}
.feature p{font-size:11px;opacity:.95;margin-top:4px}
.benefits-copy{position:absolute;left:650px;top:0;width:390px}
.benefits-copy h2{font-size:34px;color:var(--navy);letter-spacing:1px;margin-bottom:22px}
.benefits-copy p{font-size:12.5px;color:var(--muted);line-height:1.7;margin-bottom:18px}
.benefits-copy .btn{margin-top:10px;padding:11px 24px}

/* products */
.products{position:absolute;top:1160px;left:0;width:1200px;height:740px;background:var(--navy);color:var(--white);text-align:center}
.products h2{font-size:38px;margin-top:82px;letter-spacing:1px}
.products .lead{font-size:13px;width:520px;margin:22px auto 0;line-height:1.7;opacity:.9}
.product-list{position:absolute;top:220px;left:152px;display:flex;gap:20px}
.product-card{width:288px;height:380px;background:var(--white);border-radius:14px 14px 40px 14px;padding:10px;color:var(--ink);text-align:center}
.product-photo{width:268px;height:156px;border-radius:10px}
.product-photo.roses{background:linear-gradient(135deg,#c3233a,#e65066)}
.product-photo.chocolate{background:linear-gradient(135deg,#b98b73,#7a4e3c)}
.product-photo.bananas{background:linear-gradient(135deg,#a7a24e,#d8c760 50%,#5f6b3a)}
.product-card h3{font-family:"Poppins",sans-serif;font-weight:500;font-size:24px;margin:18px 0 10px}
.product-card p{font-size:12px;color:var(--muted);line-height:1.6;width:200px;margin:0 auto}
.product-actions{display:flex;align-items:center;justify-content:center;gap:34px;margin-top:22px}
.btn-outline{border:1.5px solid var(--ink);padding:8px 18px;font-size:12px;border-radius:20px}

/* contact */
.contact{position:absolute;top:1990px;left:0;width:1200px;text-align:center}
.contact h2{font-size:40px;color:var(--ink);letter-spacing:2px}
.contact .lead{font-size:13px;color:var(--muted);width:520px;margin:20px auto 0;line-height:1.7}
.contact-form{position:relative;width:880px;margin:34px auto 0;text-align:left}
.field-row{display:flex;gap:60px;margin-bottom:36px}
.field{flex:1;border-bottom:1px solid var(--line);padding-bottom:14px;font-size:11px;letter-spacing:.5px;color:var(--muted)}
.field.message{height:80px}
.contact-form .btn{display:block;width:170px;margin:40px auto 0;text-align:center}

/* newsletter + footer */
.site-footer{position:absolute;top:2560px;left:0;width:1200px;height:688px;background:var(--navy-deep);color:var(--white)}
.newsletter{text-align:center;padding-top:90px}
.newsletter h2{font-size:38px;letter-spacing:2px}
.newsletter p{font-size:13px;width:520px;margin:22px auto 0;line-height:1.7;opacity:.85}
.subscribe{display:flex;width:560px;margin:36px auto 0;background:var(--white);border-radius:24px;padding:4px}
.subscribe span{flex:1;font-size:12px;color:var(--muted);padding:10px 22px;text-align:left}
.subscribe .btn{background:var(--red);color:var(--white);padding:10px 26px}
.footer-rule{position:absolute;left:160px;width:880px;height:1px;background:rgba(255,255,255,.2)}
.footer-cols{position:absolute;top:370px;left:160px;width:880px;display:flex}
.footer-brand{width:285px}
.footer-brand .brand-name{color:var(--white)}
.footer-brand p{font-size:12px;opacity:.85;line-height:1.7;margin-top:20px;width:200px}
.footer-col{width:205px}
.footer-col h3{font-family:"Poppins",sans-serif;font-size:18px;color:var(--red);font-weight:500;margin-bottom:20px}
.footer-col li{list-style:none;font-size:12px;opacity:.85;margin-bottom:10px}
.contact-info{width:230px}
.contact-info li{display:flex;gap:10px;align-items:flex-start;line-height:1.5}
.contact-info svg{flex:none;margin-top:2px}
.socials{position:absolute;top:590px;left:160px;display:flex;gap:12px}
.socials span{width:30px;height:30px;border-radius:50%;background:var(--navy)}
.socials span.accent{background:var(--red)}
.legal{position:absolute;top:656px;left:160px;width:880px;display:flex;justify-content:space-between;font-size:12px;opacity:.85}
</style>
</head>
<body>

<header class="site-header">
  <a class="brand" href="#"><span class="brand-mark"></span><span class="brand-name">Andina Trade Co.</span></a>
  <nav class="main-nav">
    <a class="active" href="#">Home</a><a href="#">About</a><a href="#">Services</a><a href="#">Experience</a>
  </nav>
  <span class="nav-phone"><svg width="16" height="16" viewBox="0 0 24 24"><path fill="#fff" d="M6.6 10.8a15.1 15.1 0 0 0 6.6 6.6l2.2-2.2c.3-.3.7-.4 1-.2 1.1.4 2.3.6 3.6.6.6 0 1 .4 1 1V20c0 .6-.4 1-1 1A17 17 0 0 1 3 4c0-.6.4-1 1-1h3.5c.6 0 1 .4 1 1 0 1.2.2 2.4.6 3.6.1.3 0 .7-.2 1z"/></svg></span>
  <a class="btn btn-dark nav-contact" href="#">Contact Us</a>
</header>

<section class="hero">
  <div class="hero-bg"></div>
  <div class="photo photo-cocoa" role="img" aria-label="Pile of Ecuadorian cocoa beans"></div>
  <div class="photo photo-roses" role="img" aria-label="Bunches of red roses"></div>
  <div class="photo photo-bananas" role="img" aria-label="Crates of yellow bananas at a market"></div>
  <div class="hero-copy">
    <h1>Exporting <span>Roses</span>,<br>Chocolate, &amp; Bananas<br><span>WorldWide.</span></h1>
    <p>Ecuador originated "Arriba nacional" products are popular and well demanded in international markets due to its best quality and criteria.</p>
    <a class="btn btn-dark" href="#">Click For Details</a>
  </div>
</section>

<section class="benefits">
  <div class="feature green">
    <span class="feature-icon"><svg width="20" height="20" viewBox="0 0 24 24"><path d="M5 12l5 5 9-10" stroke="#fff" stroke-width="2.5" fill="none"/></svg></span>
    <div><h3>Safe Ingredients</h3><p>Clean, natural crops grown with care.</p></div>
  </div>
  <div class="feature yellow">
    <span class="feature-icon"><svg width="20" height="20" viewBox="0 0 24 24"><path d="M5 12l5 5 9-10" stroke="#fff" stroke-width="2.5" fill="none"/></svg></span>
    <div><h3>Eco-friendly</h3><p>Sustainable farms and greener shipping.</p></div>
  </div>
  <div class="feature salmon">
    <span class="feature-icon"><svg width="20" height="20" viewBox="0 0 24 24"><path d="M5 12l5 5 9-10" stroke="#fff" stroke-width="2.5" fill="none"/></svg></span>
    <div><h3>100% Tested</h3><p>Every lot is checked before it leaves port.</p></div>
  </div>
  <div class="benefits-copy">
    <h2>Benefits From Us</h2>
    <p>Lorem Ipsum Dolor Sit Amet, A Ana Anima Consectetur Adipiscing Elit, Sed Do Eiusmod &amp; Tempor A Incididunt Ut Labore Et Dolore Magna Aliqua. Ut A Enim Ad Minim Veniam, Quis Nostrud Exercitation Anchation, Laboris Nisi Ut Aliquip Ex Ea Commodo Consequat.</p>
    <p>Ut Enim Ad Minim Veniam, Quisa Nostrud Exercitation Ullamco Laboris Nisi A Ut Aliquip A Ex Ea Commodo Consequat.</p>
    <a class="btn btn-dark" href="#">Read More</a>
  </div>
</section>

<section class="products">
  <h2>Products From Ecuador</h2>
  <p class="lead">Lorem Ipsum Dolor Sit Amet, Consectetur Adipiscing Elit, Sed Do Eiusmod Tempor Incididunt Ut Labore Et Dolore Magna Aliqua.</p>
  <div class="product-list">
    <article class="product-card">
      <div class="product-photo roses" role="img" aria-label="Crates of red roses"></div>
      <h3>Roses</h3>
      <p>Lorem Ipsum Is Simply Dummy Text Of The Printing And Typesetting Industry.</p>
      <div class="product-actions"><a class="btn btn-outline" href="#">Explore More</a><svg width="28" height="12" viewBox="0 0 28 12"><path d="M0 6h26M21 1l5 5-5 5" stroke="#1f2a37" stroke-width="1.6" fill="none"/></svg></div>
    </article>
    <article class="product-card">
      <div class="product-photo chocolate" role="img" aria-label="Cocoa beans in a sack"></div>
      <h3>Chocolate</h3>
      <p>Lorem Ipsum Is Simply Dummy Text Of The Printing And Typesetting Industry.</p>
      <div class="product-actions"><a class="btn btn-outline" href="#">Explore More</a><svg width="28" height="12" viewBox="0 0 28 12"><path d="M0 6h26M21 1l5 5-5 5" stroke="#1f2a37" stroke-width="1.6" fill="none"/></svg></div>
    </article>
    <article class="product-card">
      <div class="product-photo bananas" role="img" aria-label="Banana bunches hanging on a plantation"></div>
      <h3>Bananas</h3>
      <p>Lorem Ipsum Is Simply Dummy Text Of The Printing And Typesetting Industry.</p>
      <div class="product-actions"><a class="btn btn-outline" href="#">Explore More</a><svg width="28" height="12" viewBox="0 0 28 12"><path d="M0 6h26M21 1l5 5-5 5" stroke="#1f2a37" stroke-width="1.6" fill="none"/></svg></div>
    </article>
  </div>
</section>

<section class="contact">
  <h2>GET IN TOUCH</h2>
  <p class="lead">Lorem Ipsum Dolor Sit Amet, Consectetur Adipiscing Elit, Sed Do Eiusmod Tempor Incididunt Ut Labore Et Dolore Magna Aliqua.</p>
  <form class="contact-form">
    <div class="field-row"><div class="field">FIRST NAME:</div><div class="field">LAST NAME:</div></div>
    <div class="field-row"><div class="field">EMAIL ADDRESS:</div><div class="field">PHONE NUMBER:</div></div>
    <div class="field-row"><div class="field message">MESSAGE:</div></div>
    <a class="btn btn-dark" href="#">Send Message</a>
  </form>
</section>

<footer class="site-footer">
  <div class="newsletter">
    <h2>SUBSCRIBE OUR NEWSLETTER</h2>
    <p>Lorem Ipsum Dolor Sit Amet, Consectetur Adipiscing Elit, Sed Do Eiusmod Tempor Incididunt Ut Labore Et Dolore Magna Aliqua.</p>
    <div class="subscribe"><span>Enter your email address</span><a class="btn" href="#">Subscribe</a></div>
  </div>
  <div class="footer-rule" style="top:320px"></div>
  <div class="footer-cols">
    <div class="footer-brand">
      <div class="brand"><span class="brand-mark"></span><span class="brand-name">Andina Trade Co.</span></div>
      <p>Lorem Ipsum Dolor Sit Amet, Consectetur Adipiscing Elit, Sed Do Eiusmod Tempor.</p>
    </div>
    <div class="footer-col"><h3>Quick Links</h3><ul><li>Home</li><li>About</li><li>Services</li><li>Experience</li><li>Contact</li></ul></div>
    <div class="footer-col" style="width:160px"><h3>Others</h3><ul><li>Lorem</li><li>Ipsum</li><li>Dummy</li><li>Text</li><li>Free</li></ul></div>
    <div class="footer-col contact-info"><h3>Contact Info</h3><ul>
      <li><svg width="12" height="12" viewBox="0 0 24 24"><path fill="#e8343f" d="M6.6 10.8a15.1 15.1 0 0 0 6.6 6.6l2.2-2.2c.3-.3.7-.4 1-.2 1.1.4 2.3.6 3.6.6.6 0 1 .4 1 1V20c0 .6-.4 1-1 1A17 17 0 0 1 3 4c0-.6.4-1 1-1h3.5c.6 0 1 .4 1 1 0 1.2.2 2.4.6 3.6.1.3 0 .7-.2 1z"/></svg>+593 2 555 0140</li>
      <li><svg width="12" height="12" viewBox="0 0 24 24"><path fill="#e8343f" d="M2 5h20v14H2zM2 5l10 8 10-8" stroke="#0f1b2b" stroke-width="1.5"/></svg>hello@andinatrade.test</li>
      <li><svg width="12" height="12" viewBox="0 0 24 24"><path fill="#e8343f" d="M12 2a7 7 0 0 0-7 7c0 5 7 13 7 13s7-8 7-13a7 7 0 0 0-7-7zm0 9.5A2.5 2.5 0 1 1 12 6.5a2.5 2.5 0 0 1 0 5z"/></svg>Av. Los Nevados 410, Quito 170150, Ecuador</li>
    </ul></div>
  </div>
  <div class="socials"><span></span><span class="accent"></span><span class="accent"></span><span></span></div>
  <div class="footer-rule" style="top:636px"></div>
  <div class="legal"><span>Privacy &amp; Policy</span><span>© 2020, Andina Trade Co.</span></div>
</footer>

</body>
</html>
```